Website Landing Page for Medical Recruitment

Looking for a landing page to add to our existing website. The objective of the page is to recruit new clinical staff for various departments within Pinecrest Medical Center (non-profit hospital in the Richmond, TX area).

We would like the page to be modern, professional, and non-cluttered. Please include call-to-actions and include a button that will navigate to the page where candidates can submit their applications (this page already exists).

Target Market(s)

25-35-year-olds who live in the Houston and Richmond area with medical experience.

Industry/Entity Type

Medical/Health

Font styles to use
Sans Serif

Colors
0054AA
0677BA
7BADD7
CADEEF
E8F1F8

Requirements
Must have
• A "call to action"; a button that navigates to pinecrestmedhub.example/careers

```html
<!DOCTYPE html>
<html lang="en">
<head>
<meta charset="utf-8">
<title>Pinecrest Medical Center – Careers</title>
<link href="https://fonts.googleapis.com/css2?family=Work+Sans:wght@400;500;600&display=swap" rel="stylesheet">
<style>
:root{
  --navy:#0054AA;
  --blue:#0677BA;
  --sky:#7BADD7;
  --pale:#CADEEF;
  --mist:#E8F1F8;
  --ink:#1f2733;
  --body:#5f6672;
  --white:#fff;
}
*{box-sizing:border-box;margin:0;padding:0}
html,body{width:1200px;height:3992px;overflow:hidden}
body{font-family:"Work Sans",Arial,sans-serif;color:var(--ink);background:var(--white);position:relative}
a{color:inherit;text-decoration:none}
.abs{position:absolute}
.photo{position:absolute}
.brand{position:absolute;display:flex;align-items:center;gap:10px;color:var(--navy);font-size:22px;font-weight:500}
.brand-dot{width:30px;height:30px;border-radius:50%;background:var(--navy)}
.btn{position:absolute;display:flex;align-items:center;justify-content:center;background:var(--navy);color:#fff;font-size:13px;font-weight:600;letter-spacing:.5px;border-radius:4px}
.sec-head{position:absolute;display:flex;align-items:flex-start;gap:14px}
.sec-head .mark{width:42px;height:42px;border-radius:50%;background:var(--navy);margin-top:4px}
.sec-head h2{font-size:33px;font-weight:600;color:var(--navy);line-height:1.1}
.sec-head small{display:block;text-align:right;font-size:13px;color:var(--body);letter-spacing:.6px;border-top:1px solid var(--pale);padding-top:5px;margin-top:4px}
.lorem{font-size:13px;line-height:22px;color:var(--body)}

/* hero */
.hero-bg{left:0;top:0;width:1200px;height:600px;background:var(--mist)}
.hero-photo{left:525px;top:0;width:675px;height:675px;border-bottom-left-radius:190px;background:linear-gradient(160deg,#8f9aa4,#d8dde2 45%,#f0f1f2 70%,#b9c2ca)}
.nav{position:absolute;top:26px;left:727px;display:flex;gap:0}
.nav a{color:#fff;font-size:13px;width:86px;text-align:center;line-height:24px}
.nav .signup{background:var(--navy);border-radius:3px;width:82px;margin-left:10px;font-weight:500}
.hero-dash{left:898px;top:78px;width:38px;height:9px;border-radius:5px;background:#fff}
.hero h1{left:60px;top:190px;font-size:57px;line-height:72px;font-weight:600;color:var(--navy)}
.hero p{left:60px;top:340px;width:420px;font-size:16px;line-height:29px;color:var(--body)}
.search{left:60px;top:422px;width:522px;height:46px;background:#fff;border-radius:4px;box-shadow:0 4px 14px rgba(0,84,170,.08);display:flex;align-items:center;padding-left:16px;font-size:12px;color:var(--body);gap:12px}
.search .ring{width:20px;height:20px;border:1.5px solid var(--navy);border-radius:50%}
.search .btn{right:4px;top:4px;width:120px;height:38px;position:absolute}

/* features */
.feature{position:absolute;top:830px;width:350px;text-align:center}
.feature .icon{width:104px;height:104px;border-radius:10px;background:var(--mist);margin:0 auto;display:flex;align-items:center;justify-content:center}
.feature h3{margin-top:26px;font-size:17px;font-weight:500}
.feature .bar{width:18px;height:2px;background:var(--navy);margin:12px auto 14px}

/* about */
.about-band{left:0;top:1247px;width:640px;height:403px;background:var(--mist)}
.about-photo{left:622px;top:1212px;width:578px;height:413px;background:linear-gradient(135deg,#3b3f45,#6d8ea0 40%,#5bbccb 65%,#c9d4dc)}
.play{left:619px;top:1567px;width:54px;height:54px;border-radius:50%;background:var(--navy);display:flex;align-items:center;justify-content:center}

/* jobs */
.jobs-band{left:460px;top:1700px;width:740px;height:432px;background:var(--mist)}
.jobs-photo{left:0;top:1700px;width:525px;height:460px;border-bottom-right-radius:70px;background:linear-gradient(120deg,#d9c1bd,#c98ab4 35%,#eef1f4 60%,#c9d3dc)}
.job{position:absolute;top:1808px;width:330px;height:249px;background:#fff;box-shadow:0 6px 18px rgba(0,40,90,.08);padding:30px}
.job .jicon{position:absolute;left:30px;top:30px;width:58px;height:58px;border-radius:6px;background:var(--mist);display:flex;align-items:center;justify-content:center}
.job h4{margin-left:75px;font-size:17px;font-weight:500;margin-top:8px}
.job .sub{margin-left:75px;font-size:11px;margin-top:8px;color:var(--ink)}
.job .lorem{margin-top:28px;font-size:12px;line-height:24px}
.job .apply{display:inline-block;margin-top:16px;font-size:12px;font-weight:600;color:var(--navy);border-bottom:2px solid var(--navy);padding-bottom:2px}

/* testimonial */
.testi-photo{left:60px;top:2237px;width:1080px;height:450px;border-top-left-radius:80px;background:radial-gradient(circle at 65% 50%,#1aa4e8,#0b8ad6 45%,#0677BA)}
.testi-card{left:135px;top:2342px;width:345px;height:413px;background:#fff;border-bottom-right-radius:70px;box-shadow:0 8px 24px rgba(0,0,0,.05);padding:42px 45px}
.testi-card .sec-head{position:static}
.dots{display:flex;gap:8px;margin:30px 0 20px}
.dots i{width:18px;height:2px;background:var(--pale)}
.dots i:first-child{background:var(--navy)}
.quote{font-size:15px;line-height:26px;color:var(--body)}
.cite{margin-top:12px;font-size:12px;color:var(--body)}
.cite b{color:var(--navy);font-weight:500}

/* blog */
.post-img{position:absolute;top:2935px;width:262px;height:293px;border-top-right-radius:46px}
.post-card{position:absolute;top:2983px;width:300px;height:202px;background:#fff;box-shadow:0 6px 22px rgba(0,40,90,.08);padding:26px 22px}
.post-card .date{font-size:11px;color:var(--navy);display:flex;align-items:center;gap:8px}
.post-card h5{font-size:15px;font-weight:500;line-height:26px;margin:12px 0 8px;letter-spacing:-.3px}
.post-card .lorem{font-size:11.5px;line-height:24px}

/* join */
.join-photo{left:0;top:3303px;width:1200px;height:480px;background:linear-gradient(90deg,#3d5870,#5f7b92 30%,#4d6a86 60%,#6d8aa1)}
.join-text{left:0;top:3474px;width:1200px;text-align:center;color:#fff}
.join-text small{font-size:15px}
.join-text h2{font-size:38px;font-weight:600;margin-top:6px}
.join .btn{left:540px;top:3572px;width:120px;height:36px;background:#fff;color:var(--navy);border-radius:3px}

/* footer */
.foot-links{position:absolute;left:374px;top:3862px;display:flex;font-size:11px;color:var(--body)}
.foot-links a{margin-right:42px}
.social{position:absolute;top:3855px;width:33px;height:33px;border:1.5px solid var(--navy);border-radius:3px}
.social.filled{background:var(--navy)}
.rule{left:60px;top:3943px;width:1080px;height:1px;background:var(--mist)}
.copy{left:0;top:3955px;width:1200px;text-align:center;font-size:11px;color:var(--body)}
.copy b{color:var(--navy);font-weight:500}
</style>
</head>
<body>

<!-- Hero -->
<section class="hero">
  <div class="abs hero-bg"></div>
  <div class="photo hero-photo" role="img" aria-label="Two doctors in white coats reviewing a tablet and clipboard in a hospital corridor"></div>
  <a class="brand" style="left:60px;top:18px" href="#"><span class="brand-dot"></span>Pinecrest Medical Center</a>
  <nav class="nav">
    <a href="#">About</a><a href="#">Careers</a><a href="#">Contact</a><a href="#">Login</a><a class="signup" href="#">Sign Up</a>
  </nav>
  <div class="abs hero-dash"></div>
  <h1 class="abs">Recruiting New<br>Clinical Staff</h1>
  <p class="abs">Lorem ipsum dolor sit amet, consectetuer adipiscing elit, sed diam nonummy nibh euismod tincidunt.</p>
  <div class="abs search"><span class="ring"></span>Search By Keyword<a class="btn" href="https://pinecrestmedhub.example/careers">SEARCH JOB</a></div>
</section>

<!-- Features -->
<section class="features">
  <div class="sec-head" style="left:432px;top:748px"><span class="mark"></span><div><h2>How Can We Help</h2><small>OUR FEATURES</small></div></div>
  <div class="feature" style="left:57px">
    <div class="icon"><svg width="56" height="56" viewBox="0 0 56 56" fill="none" stroke="#0054AA" stroke-width="2"><circle cx="28" cy="16" r="8"/><path d="M14 50v-10a14 14 0 0 1 28 0v10"/><circle cx="10" cy="30" r="5"/><circle cx="46" cy="30" r="5"/></svg></div>
    <h3>Daily Supply Work</h3><div class="bar"></div>
    <p class="lorem">Lorem ipsum dolor sit amet, consectetuer adipiscing elit, sed diam nonummy nibh euismod tincidunt ut laoreet dolore magna aliquam erat volutpat.</p>
  </div>
  <div class="feature" style="left:424px">
    <div class="icon"><svg width="60" height="56" viewBox="0 0 60 56" fill="none" stroke="#0054AA" stroke-width="2"><path d="M10 10h40M44 5l6 5-6 5"/><rect x="18" y="22" width="34" height="28" rx="2"/><path d="M18 30h34M26 36h4M34 36h4M42 36h4M26 43h4M34 43h4M42 43h4"/><circle cx="14" cy="38" r="9" fill="#E8F1F8"/><path d="M14 33v5l3 2"/></svg></div>
    <h3>Long-Term Roles</h3><div class="bar"></div>
    <p class="lorem">Lorem ipsum dolor sit amet, consectetuer adipiscing elit, sed diam nonummy nibh euismod tincidunt ut laoreet dolore magna aliquam erat volutpat.</p>
  </div>
  <div class="feature" style="left:792px">
    <div class="icon"><svg width="56" height="56" viewBox="0 0 56 56" fill="none" stroke="#0054AA" stroke-width="2"><rect x="8" y="6" width="32" height="42" rx="2"/><path d="M14 16h20M14 22h20M14 28h14M14 34h10"/><circle cx="40" cy="40" r="10" fill="#E8F1F8"/><path d="M35 40l4 4 6-7"/></svg></div>
    <h3>A Permanent Job</h3><div class="bar"></div>
    <p class="lorem">Lorem ipsum dolor sit amet, consectetuer adipiscing elit, sed diam nonummy nibh euismod tincidunt ut laoreet dolore magna aliquam erat volutpat.</p>
  </div>
  <a class="btn" style="left:540px;top:1100px;width:120px;height:37px" href="https://pinecrestmedhub.example/careers">APPLY NOW</a>
</section>

<!-- About -->
<section class="about">
  <div class="abs about-band"></div>
  <div class="photo about-photo" role="img" aria-label="Nurses and a doctor in scrubs looking at a tablet together"></div>
  <div class="abs play"><svg width="18" height="20" viewBox="0 0 18 20"><path d="M2 1l15 9-15 9z" fill="#fff"/></svg></div>
  <div class="sec-head" style="left:60px;top:1290px"><span class="mark"></span><div><h2>About Pinecrest</h2><small>MEDICAL CENTER</small></div></div>
  <div class="abs" style="left:60px;top:1370px;width:420px">
    <p style="font-size:14px;font-weight:500">We Make Relationship Between Medical Center &amp; Staff</p>
    <p class="lorem" style="font-size:12px;margin-top:8px">Lorem ipsum dolor sit amet, consectetuer adipiscing elit, sed diam nonummy nibh euismod tincidunt ut laoreet dolore magna aliquam erat volutpat.</p>
    <p class="lorem" style="font-size:12px;margin-top:4px">Ut wisi enim ad minim veniam, quis nostrud exerci tation ullamcorper suscipit lobortis nisl ut aliquip ex ea commodo consequat.</p>
  </div>
  <a class="btn" style="left:60px;top:1538px;width:120px;height:37px" href="#">READ MORE</a>
</section>

<!-- Job offers -->
<section class="jobs">
  <div class="abs jobs-band"></div>
  <div class="photo jobs-photo" role="img" aria-label="Doctor with clipboard speaking with a pregnant patient"></div>
  <div class="sec-head" style="left:620px;top:1725px"><span class="mark"></span><div><h2>Pinecrest Job Offers</h2><small>CAREER OPTIONS</small></div></div>
  <article class="job" style="left:465px">
    <div class="jicon"><svg width="34" height="34" viewBox="0 0 34 34" fill="none" stroke="#0054AA" stroke-width="1.8"><circle cx="17" cy="12" r="6"/><path d="M11 12c-5 0-7-4-5-7M23 12c5 0 7-4 5-7M17 18v12M13 26h8"/></svg></div>
    <h4>Gynecologist</h4><p class="sub">Lorem ipsum</p>
    <p class="lorem">Lorem ipsum dolor sit amet, consectetuer adipiscing elit, sed diam nonummy nibh euismod tincidunt ut laoreet dolore.</p>
    <a class="apply" href="https://pinecrestmedhub.example/careers">APPLY NOW</a>
  </article>
  <article class="job" style="left:810px">
    <div class="jicon"><svg width="34" height="34" viewBox="0 0 34 34" fill="none" stroke="#0054AA" stroke-width="1.8"><circle cx="17" cy="17" r="13"/><circle cx="17" cy="17" r="8"/><path d="M17 11v12M13 15h8"/></svg></div>
    <h4>Physiotherapist</h4><p class="sub">Lorem ipsum</p>
    <p class="lorem">Lorem ipsum dolor sit amet, consectetuer adipiscing elit, sed diam nonummy nibh euismod tincidunt ut laoreet dolore.</p>
    <a class="apply" href="https://pinecrestmedhub.example/careers">APPLY NOW</a>
  </article>
  <article class="job" style="left:1155px"></article>
</section>

<!-- Testimonials -->
<section class="testi">
  <div class="photo testi-photo" role="img" aria-label="Smiling nurse in navy scrubs with a stethoscope against a blue wall"></div>
  <div class="abs testi-card">
    <div class="sec-head"><span class="mark"></span><div><h2>Testimonials</h2><small>CLIENTS REVIEW</small></div></div>
    <div class="dots"><i></i><i></i><i></i></div>
    <p class="quote">“Lorem ipsum dolor sit amet, contetuer adipiscing elit, sed diam nonummy nibh euismod tincidunt ut laoreet dolore magna aliquam erat volutpat. Ut wisi enim ad minim veniam, quis nostrud exerci tation ullamcorper.</p>
    <p class="cite"><b>Dana Whitfield,</b> Ceo Of Lakeside Hospital</p>
  </div>
</section>

<!-- Blog -->
<section class="blog">
  <div class="sec-head" style="left:440px;top:2828px"><span class="mark"></span><div><h2>Latest Blog Posts</h2><small>Recent Updates</small></div></div>
  <div class="post-img" style="left:60px;background:linear-gradient(135deg,#1c3d66,#4a7fb5 50%,#a9c6df)" role="img" aria-label="Surgeons operating under theatre lights"></div>
  <article class="post-card" style="left:285px">
    <p class="date"><svg width="13" height="13" viewBox="0 0 13 13" fill="none" stroke="#0054AA"><rect x="1" y="2" width="11" height="10"/><path d="M1 5h11M4 0v3M9 0v3"/></svg>2 August 2022</p>
    <h5>Lorem ipsum dolor sit amet, contuer adipiscing elit, sed diam nonummy.</h5>
    <p class="lorem">Lorem ipsum dolor sit amet, contetuer adipiscing elit, sed diam nonummy nibh euismod tincidunt ut laoreet dolore.</p>
  </article>
  <div class="post-img" style="left:615px;background:linear-gradient(135deg,#5b6570,#c8d0d8 50%,#eef0f2)" role="img" aria-label="Medical staff walking through a hospital corridor"></div>
  <article class="post-card" style="left:840px">
    <p class="date"><svg width="13" height="13" viewBox="0 0 13 13" fill="none" stroke="#0054AA"><rect x="1" y="2" width="11" height="10"/><path d="M1 5h11M4 0v3M9 0v3"/></svg>2 August 2022</p>
    <h5>Lorem ipsum dolor sit amet, contuer adipiscing elit, sed diam nonummy.</h5>
    <p class="lorem">Lorem ipsum dolor sit amet, contetuer adipiscing elit, sed diam nonummy nibh euismod tincidunt ut laoreet dolore.</p>
  </article>
</section>

<!-- Join -->
<section class="join">
  <div class="photo join-photo" role="img" aria-label="Group of smiling doctors and nurses in scrubs standing together"></div>
  <div class="abs join-text"><small>We Offer Jobs For All Medical Staffs</small><h2>Join Our Team Today</h2></div>
  <a class="btn" href="https://pinecrestmedhub.example/careers">APPLY NOW</a>
</section>

<!-- Footer -->
<footer>
  <a class="brand" style="left:60px;top:3845px" href="#"><span class="brand-dot"></span>Pinecrest Medical Center</a>
  <nav class="foot-links"><a href="#">About</a><a href="#">Careers</a><a href="#">Contact</a><a href="#">Privacy Policy</a><a href="#">Terms &amp; Conditions</a></nav>
  <a class="social filled" style="left:1019px" href="#" aria-label="Social profile"></a>
  <a class="social" style="left:1063px" href="#" aria-label="Social profile"></a>
  <a class="social" style="left:1107px" href="#" aria-label="Social profile"></a>
  <div class="abs rule"></div>
  <p class="abs copy">© <b>Pinecrest Medical Center</b> - 2022. All Rights Reserved.</p>
</footer>

</body>
</html>
```